Flyer for Tallow Brisko - Design Agency

We need a 4-page square flyer measuring 14.8x14.8cm per page, to fold out, for a design agency targeting small businesses.
The design should be very modern. There shouldn't be too much content visible.
The background should be black. The color of the logo (attached) can also be used. The content is also attached and divided per page. We are open to alternative suggestions regarding the division.

```html
<!DOCTYPE html>
<html lang="de">
<head>
<meta charset="utf-8">
<title>Tallow Brisko – Faltflyer</title>
<link href="https://fonts.googleapis.com/css2?family=Quicksand:wght@300;400;500&display=swap" rel="stylesheet">
<style>
  :root{
    --stage:#cfcfcf;
    --paper-outer:#0b0b0b;
    --paper-inner:#141414;
    --fold:#1c1c1c;
    --brand:#8fd0ea;
    --text:#e8e8e8;
    --muted:#8c8c8c;
    --ghost:#333333;
  }
  *{box-sizing:border-box;margin:0;padding:0}
  html,body{width:1200px;height:900px;overflow:hidden;background:var(--stage)}
  body{font-family:"Quicksand",sans-serif;position:relative}
  .spread{position:absolute;left:190px;width:820px;height:410px;display:flex}
  .spread--outer{top:22px}
  .spread--inner{top:468px}
  .page{position:relative;width:410px;height:410px}
  .spread--outer .page{background:var(--paper-outer)}
  .spread--inner .page{background:var(--paper-inner)}
  .page + .page{border-left:1px solid var(--fold)}

  .brand-name{color:var(--brand);font-weight:500;letter-spacing:.5px;text-align:center;position:absolute;left:0;right:0}
  .brand-name--small{top:160px;font-size:22px}
  .brand-name--cover{top:66px;font-size:38px;line-height:1}

  .contact{position:absolute;left:0;right:0;top:216px;text-align:center;font-size:8.4px;font-weight:300;line-height:18px;text-transform:uppercase;color:var(--text);letter-spacing:.2px}
  .contact .lead{color:var(--muted)}
  .owners{position:absolute;left:0;right:0;top:364px;text-align:center;font-size:8px;color:var(--muted);text-transform:uppercase;font-weight:300}

  .cover-photo{position:absolute;left:70px;top:160px;width:270px;height:150px;border-radius:50%;
    background:radial-gradient(ellipse at 40% 55%,#c23a55 0%,#5a2a6a 35%,#1a1a2a 62%,rgba(11,11,11,0) 75%)}
  .tagline{position:absolute;left:0;right:0;top:362px;text-align:center;font-size:8px;color:var(--muted);text-transform:uppercase;font-weight:300}

  .ghost-name{position:absolute;left:22px;right:22px;top:55px;color:var(--ghost);font-weight:400;font-size:118px;line-height:.92;letter-spacing:-2px;text-align:center}
  .intro{position:absolute;left:0;right:0;top:300px;text-align:center;color:var(--text)}
  .intro h2{font-weight:400;font-size:13.5px;line-height:17px}
  .intro p{margin-top:14px;font-size:8.4px;font-weight:300;line-height:11px}

  .section-title{position:absolute;left:14px;font-size:12px;font-weight:400;color:var(--text);text-transform:uppercase}
  .services{position:absolute;left:14px;top:82px;width:380px;display:grid;grid-template-columns:1fr 1fr;row-gap:28px;column-gap:14px}
  .service{display:flex;gap:8px}
  .service .num{font-size:18px;font-weight:300;color:var(--text);line-height:1;padding-top:2px;width:14px}
  .service h3{font-size:8.4px;font-weight:400;color:var(--text);line-height:11px}
  .service p{font-size:8.4px;font-weight:300;color:var(--brand);line-height:11px}
  .reasons{position:absolute;left:16px;top:294px;width:380px;display:grid;grid-template-columns:1fr 1fr;column-gap:14px}
  .reason{display:flex;gap:8px}
  .reason svg{flex:none;width:22px;height:22px}
  .reason h3{font-size:8.4px;font-weight:400;color:var(--text);line-height:11px}
  .reason p{font-size:8.6px;font-weight:300;color:var(--brand);line-height:12px}
  .closing{position:absolute;left:0;right:0;top:360px;text-align:center;font-size:8.6px;color:var(--text);letter-spacing:1.2px;font-weight:300}
</style>
</head>
<body>

<section class="spread spread--outer">
  <article class="page page--back">
    <div class="brand-name brand-name--small">Tallow Brisko</div>
    <div class="contact">
      <div class="lead">Kontaktiere uns für eine kostenlose Beratung!</div>
      <div>+49 000 11223 &nbsp;|&nbsp; design@tallowbrisko.de</div>
      <div>Lindenweg 8, 60311 Frankfurt</div>
    </div>
    <div class="owners">Inhaber : Jonas Merel &amp; Ida Fenwick</div>
  </article>
  <article class="page page--cover">
    <div class="brand-name brand-name--cover">Tallow<br>Brisko</div>
    <div class="cover-photo" role="img" aria-label="Foto eines aufgeklappten Laptops im Dunkeln mit rot-blauem Bildschirmleuchten"></div>
    <div class="tagline">Designs, die wirken. Marken, die bleiben.</div>
  </article>
</section>

<section class="spread spread--inner">
  <article class="page page--intro">
    <div class="ghost-name" aria-hidden="true">Tallow<br>Brisko</div>
    <div class="intro">
      <h2>Tallow Brisko gestaltet die Zukunft deines<br>Unternehmensauftritts.</h2>
      <p>Wir machen aus Ideen visuelle Erlebnisse und sorgen dafür,<br>dass deine Marke im Gedächtnis bleibt.</p>
    </div>
  </article>
  <article class="page page--services">
    <h2 class="section-title" style="top:40px">Unsere Leistungen:</h2>
    <div class="services">
      <div class="service"><span class="num">1</span><div><h3>Next-Level Flyer</h3><p>Nicht nur Papier, sondern deine Botschaft im perfekten Look.</p></div></div>
      <div class="service"><span class="num">2</span><div><h3>Corporate Identity</h3><p>Ein Design, das deine Marke spricht – individuell, stark, unvergesslich.</p></div></div>
      <div class="service"><span class="num">3</span><div><h3>Digital &amp; Print</h3><p>Ob Social Media Grafiken oder klassisches Printdesign – wir sind da, wo du uns brauchst.</p></div></div>
      <div class="service"><span class="num">4</span><div><h3>Alles aus einer Hand</h3><p>Logo, Farben, Typografie, Flyer und vieles mehr – wir bauen das Fundament für deinen Erfolg.</p></div></div>
    </div>
    <h2 class="section-title" style="top:250px;left:19px">Warum wir?</h2>
    <div class="reasons">
      <div class="reason">
        <svg viewBox="0 0 22 22" fill="none" stroke="var(--brand)" stroke-width="1.3"><path d="M19 8.5A9 9 0 1 1 14.5 3"/><path d="M6.5 10.5l4 4L20 4"/></svg>
        <div><h3>Dein Style, unser Know-how</h3><p>Wir kombinieren deine Vision mit moderner Ästhetik.</p></div>
      </div>
      <div class="reason">
        <svg viewBox="0 0 22 22" fill="none" stroke="var(--brand)" stroke-width="1.3"><path d="M19 8.5A9 9 0 1 1 14.5 3"/><path d="M6.5 10.5l4 4L20 4"/></svg>
        <div><h3>Persönlicher Service</h3><p>Wir hören zu und setzen um, was dich einzigartig macht</p></div>
      </div>
    </div>
    <div class="closing">Flexible Lösungen für die unterschiedlichsten Anforderungen</div>
  </article>
</section>

</body>
</html>
```